Business card for Crestline Bathrooms

Please design a business card for our bathroom renovation business. You can use my existing logo, but if you have an idea to modernize it, I would like to see it. Please see attached files first. I would like to use the blue and the orange theme. I like the concept of using the shower head in the logo. Please find following a design (or two) that I have been trying to create with my limited resources. That design was for a sign, but I was going to adopt it and use it as a business card as well. I like the concept of the water splash but I don’t think it “flows” nicely together with the logo. Another thought is that maybe creating the logo out of water splash could work and have a dramatic effect (like the water text and the butterfly picture attached with similar background instead of white). If the above doesn’t work I would like to see a modern simplified design. One of the attached files named as the unwanted business card has all the details that I want included in the business card. Please note that it is two sided.
Updates

I am very thankful for the designs that I have received, but they are very similar and only a couple of attempts to do something with the water splash as per my original brief. Modernizing the logo and having it made out of out of water splash with the orange as color accent could work and have a dramatic effect (like the water text and the butterfly picture attached with similar background instead of white). Please do not use the butterfly itself! This is just an example that images can be created out of water splash.

Contact Information for Business Card

all the details are on the unwonted business card file included

Colors
3176b5

Requirements
Nice to have
• Copied from the brief:
• ... maybe creating the logo out of water splash could work and have a dramatic effect (like the water text and the butterfly picture attached with similar background instead of white). Please do not use the butterfly itself!
Should not have
• I am getting designs with a butterfly. The butterfly picture was an example of creating something from a water splash. The butterfly itself has no association with anything other than the concept of creating a logo out of water splash. Sorry, I thought I was clear in the brief.

```html
<!DOCTYPE html>
<html lang="en">
<head>
<meta charset="utf-8">
<title>Crestline Bathrooms – Business Card</title>
<link rel="stylesheet" href="https://fonts.googleapis.com/css2?family=Work+Sans:wght@400;500;600&display=swap">
<style>
  :root {
    --navy: #1d4a70;
    --navy-deep: #163c5e;
    --blue: #2c5f88;
    --coral: #e8766a;
    --white: #ffffff;
    --ink: #2f3a44;
    --mist: #e9edf1;
    --page: #d9dcdf;
  }
  * { box-sizing: border-box; margin: 0; padding: 0; }
  html, body { width: 1200px; height: 900px; overflow: hidden; }
  body {
    background: var(--page);
    font-family: "Work Sans", Arial, sans-serif;
    position: relative;
  }
  .card {
    position: absolute;
    left: 240px;
    width: 720px;
    height: 412px;
    border-radius: 22px;
    overflow: hidden;
    box-shadow: 0 6px 18px rgba(0,0,0,0.18);
  }

  /* Back side */
  .card--back { top: 28px; background: var(--white); }
  .card--back .brand-name {
    position: absolute; left: 52px; top: 52px;
    font-size: 34px; font-weight: 600; color: var(--navy);
    display: flex; align-items: center; gap: 12px;
  }
  .brand-dot { width: 16px; height: 16px; border-radius: 50%; background: var(--coral); }
  .divider-vertical {
    position: absolute; left: 440px; top: 42px;
    width: 2px; height: 120px; background: var(--navy);
  }
  .badge { position: absolute; background: var(--navy); }
  .badge--builders { left: 480px; top: 58px; width: 190px; height: 40px; border-radius: 4px; }
  .badge--institute { left: 555px; top: 112px; width: 40px; height: 40px; border-radius: 50%; }
  .services {
    position: absolute; left: 52px; top: 190px;
    list-style: none;
    font-size: 17px; font-weight: 500; color: var(--ink);
    letter-spacing: 0.3px; line-height: 1.75;
    text-transform: uppercase;
  }
  .services li::before { content: "> "; color: var(--ink); }

  /* Front side */
  .card--front {
    top: 464px;
    background: linear-gradient(160deg, var(--navy-deep) 0%, var(--blue) 100%);
    color: var(--white);
  }
  .splash-area {
    position: absolute; left: 250px; top: 0; width: 360px; height: 412px;
    background: radial-gradient(ellipse at 50% 55%, rgba(120,160,195,0.35) 0%, rgba(120,160,195,0.12) 45%, rgba(0,0,0,0) 70%);
  }
  .card--front .brand-name {
    position: absolute; left: 52px; top: 70px;
    font-size: 36px; font-weight: 600; color: var(--white);
    display: flex; align-items: center; gap: 12px;
  }
  .rule {
    position: absolute; left: 52px; top: 200px; width: 616px; height: 1.5px;
    background: var(--white);
  }
  .contact {
    position: absolute; left: 52px; top: 220px;
    list-style: none; font-size: 18px; line-height: 1.6;
  }
  .contact li { display: flex; align-items: center; gap: 10px; white-space: nowrap; }
  .contact svg { width: 14px; height: 14px; flex: none; }
  .holder {
    position: absolute; right: 52px; top: 236px; text-align: right;
  }
  .holder-name {
    font-size: 26px; font-weight: 600; letter-spacing: 1px; text-transform: uppercase;
    white-space: nowrap;
  }
  .holder-rule { width: 240px; height: 1.5px; background: var(--white); margin: 10px 0 12px auto; }
  .holder-address { font-size: 20px; line-height: 1.3; }
  .edge-band { position: absolute; left: 0; bottom: 0; width: 720px; height: 80px; }
</style>
</head>
<body>

  <section class="card card--back" aria-label="Card back">
    <div class="brand-name"><span class="brand-dot"></span>Crestline Bathrooms</div>
    <div class="divider-vertical"></div>
    <div class="badge badge--builders" aria-hidden="true"></div>
    <div class="badge badge--institute" aria-hidden="true"></div>
    <ul class="services">
      <li>Complete bathroom renovations &amp; remodelling</li>
      <li>Highly skilled &amp; qualified tradespeople</li>
      <li>Professional service from concept to completion</li>
      <li>All work guaranteed</li>
    </ul>
  </section>

  <section class="card card--front" aria-label="Card front">
    <div class="splash-area" role="img" aria-label="Water splash photograph in blue tones"></div>
    <div class="brand-name"><span class="brand-dot"></span>Crestline Bathrooms</div>
    <div class="rule"></div>
    <ul class="contact">
      <li>
        <svg viewBox="0 0 16 16" aria-hidden="true"><path d="M4 1l3 3-2 2a9 9 0 0 0 5 5l2-2 3 3-2 3C7 15 1 9 1 3z" fill="none" stroke="#fff" stroke-width="1.4"/></svg>
        0400 555 218 | 6200 4417
      </li>
      <li>
        <svg viewBox="0 0 16 16" aria-hidden="true"><rect x="1" y="3" width="14" height="10" fill="none" stroke="#fff" stroke-width="1.4"/><path d="M1 3l7 6 7-6" fill="none" stroke="#fff" stroke-width="1.4"/></svg>
        daniel@crestlinebathrooms.com.au
      </li>
      <li>
        <svg viewBox="0 0 16 16" aria-hidden="true"><circle cx="8" cy="8" r="6.5" fill="none" stroke="#fff" stroke-width="1.3"/><path d="M1.5 8h13M8 1.5c-3 3-3 10 0 13M8 1.5c3 3 3 10 0 13" fill="none" stroke="#fff" stroke-width="1.1"/></svg>
        www.crestlinebathrooms.com.au
      </li>
    </ul>
    <div class="holder">
      <div class="holder-name">Daniel Moretti</div>
      <div class="holder-rule"></div>
      <div class="holder-address">PO Box 48<br>Kellmore 2640</div>
    </div>
    <svg class="edge-band" viewBox="0 0 720 80" preserveAspectRatio="none" aria-hidden="true">
      <polygon points="0,48 330,78 330,80 0,80" fill="var(--white)"/>
      <polygon points="345,80 400,44 720,44 720,80" fill="var(--coral)"/>
    </svg>
  </section>

</body>
</html>
```